BildeVOLD buisnesscard

Hey :) I need a modern buisnesscard for my company BildeVOLD
It most have:
Dagligleder og Fotograf: Henrik Audun Strandvik

Mob: +4791264085
Epost: post@bildevold.example
Adresse: Kvernbakken9, 6040 Fjordvik

Facbook and instagram logo with text BildeVOLD

BildeVOLD logo

It Company

```html
<!DOCTYPE html>
<html lang="no">
<head>
<meta charset="utf-8">
<title>BildeVOLD – visittkort</title>
<link href="https://fonts.googleapis.com/css2?family=Source+Sans+3:wght@400;600;700&display=swap" rel="stylesheet">
<style>
  :root {
    --brand-blue: #2581b8;
    --brand-pink: #c8407f;
    --ink: #555a5f;
    --paper: #ffffff;
    --backdrop: #ececec;
    --rule-blue: #7fb3d6;
  }
  * { box-sizing: border-box; margin: 0; padding: 0; }
  html, body {
    width: 1105px; height: 1200px; overflow: hidden;
    background: var(--backdrop);
    font-family: "Source Sans 3", "Myriad Pro", sans-serif;
  }
  .canvas { position: relative; width: 1105px; height: 1200px; }
  .card {
    position: absolute; left: 193px; width: 720px; height: 412px;
    background: var(--paper);
    box-shadow: 0 4px 14px rgba(0,0,0,0.18);
    overflow: hidden;
  }
  .card--front { top: 167px; }
  .card--back { top: 623px; }

  .brand-mark {
    position: absolute; left: 138px; top: 48px;
    width: 72px; height: 72px; background: var(--brand-pink);
  }
  .brand-name {
    position: absolute; left: 40px; top: 136px;
    font-size: 48px; line-height: 52px; font-weight: 700; color: var(--brand-blue);
    letter-spacing: 0.5px;
  }

  .address {
    position: absolute; left: 41px; top: 228px;
    font-size: 19px; line-height: 26px; color: var(--ink);
  }
  .contact {
    position: absolute; left: 41px; font-size: 19px; color: var(--ink);
    display: flex; align-items: center; gap: 10px;
  }
  .contact--phone { top: 290px; }
  .contact--mail { top: 320px; }
  .contact svg { width: 16px; height: 20px; fill: var(--brand-blue); }

  .person {
    position: absolute; right: 43px; top: 258px; text-align: right;
  }
  .person__name { font-size: 27px; font-weight: 600; color: var(--brand-blue); line-height: 32px; }
  .person__title { font-size: 20px; color: var(--brand-pink); line-height: 30px; }

  .footer-band { position: absolute; left: 0; bottom: 0; width: 720px; height: 46px; }
  .website {
    position: absolute; right: 40px; bottom: 12px;
    font-size: 17px; letter-spacing: 3px; color: var(--paper);
  }

  .back-name {
    position: absolute; left: 0; right: 0; top: 150px; text-align: center;
    font-size: 72px; font-weight: 700; color: var(--brand-blue);
  }
  .social {
    position: absolute; left: 196px; width: 329px; top: 340px;
    display: flex; align-items: center; gap: 12px;
  }
  .social__rule {
    flex: 1; height: 2px;
    background: linear-gradient(90deg, transparent, var(--rule-blue));
  }
  .social__rule--right { background: linear-gradient(90deg, var(--rule-blue), transparent); }
  .social__handle {
    display: flex; align-items: center; gap: 6px;
    font-size: 17px; font-weight: 600; color: var(--brand-blue);
  }
  .social__dot { width: 12px; height: 12px; border-radius: 50%; background: var(--brand-blue); }
</style>
</head>
<body>
<main class="canvas">
  <section class="card card--front">
    <div class="brand-mark"></div>
    <div class="brand-name">BildeVOLD</div>

    <p class="address">Kvernbakken9<br>6040 Fjordvik</p>

    <p class="contact contact--phone">
      <svg viewBox="0 0 16 20" aria-hidden="true"><path d="M3 0h10a2 2 0 0 1 2 2v16a2 2 0 0 1-2 2H3a2 2 0 0 1-2-2V2a2 2 0 0 1 2-2zm0 3v12h10V3zm5 13.2a1 1 0 1 0 0 2 1 1 0 0 0 0-2z"/></svg>
      +4791264085
    </p>
    <p class="contact contact--mail">
      <svg viewBox="0 0 16 20" aria-hidden="true"><path d="M0 6h16v10H0zm1.5 1.3L8 11.6l6.5-4.3z"/></svg>
      post@bildevold.example
    </p>

    <div class="person">
      <p class="person__name">Henrik Audun Strandvik</p>
      <p class="person__title">Dagligleder og Fotograf</p>
    </div>

    <svg class="footer-band" viewBox="0 0 720 46" aria-hidden="true">
      <rect x="0" y="15" width="395" height="8" fill="var(--brand-pink)"/>
      <rect x="0" y="28" width="395" height="5" fill="var(--brand-blue)"/>
      <polygon points="408,46 428,0 720,0 720,46" fill="var(--brand-blue)"/>
    </svg>
    <p class="website">www.bildevold.example</p>
  </section>

  <section class="card card--back">
    <div class="back-name">BildeVOLD</div>
    <div class="social">
      <span class="social__rule"></span>
      <span class="social__handle"><span class="social__dot"></span>BildeVOLD</span>
      <span class="social__rule social__rule--right"></span>
    </div>
  </section>
</main>
</body>
</html>
```